Podiatry clinic requires a modern revamp and editing of existing website.

I would like a fresh new look and updated information for my current business website. An easy to navigate site with prominent address and phone number for call to action. We are a podiatry clinic that focuses on general and sports podiatry.
I would like 4 pages; including Home page, About Us, Services & Contact.
www.brambleridgepodiatry.net

Target Market(s)

Active working professionals.

Industry/Entity Type

Medical

Coding

Coded - Design and coding required

Number of Pages Required

4 page

Font styles to use
Sans Serif

Colors
6b449b

Requirements
Must have
• A modern look with logo and active images; clean and uncluttered. Visible phone number and address for call to action.
• 4 pages - Home, About Us, Services, Contact.
• Home page - update address & service logos.
• About Us - update of personal information.
• Services - Revamp of existing page.
• Contact page to include Google map, email & phone number.
Nice to have
• Ability to add content easily; eg. a blog or adding video onto Home page.
• Link to Like Us page.

```html
<!DOCTYPE html>
<html lang="en">
<head>
<meta charset="utf-8">
<title>Bramble Ridge Podiatry</title>
<link href="https://fonts.googleapis.com/css2?family=Raleway:wght@300;400;500;700;800&family=Open+Sans:wght@400;600;700&display=swap" rel="stylesheet">
<style>
:root{
  --purple:#4a2e8f;
  --purple-mid:#6b449b;
  --purple-dark:#3f2a82;
  --orange:#f47a20;
  --green:#7cc242;
  --grey-bg:#f0f0f0;
  --grey-card:#e6e6e6;
  --text:#555;
  --white:#fff;
}
*{margin:0;padding:0;box-sizing:border-box}
html,body{width:1200px;height:2795px;overflow:hidden}
body{position:relative;font-family:'Open Sans',sans-serif;color:var(--text);background:var(--white)}
.abs{position:absolute}

/* hero */
.hero{left:0;top:0;width:1200px;height:801px;
  background:linear-gradient(180deg,#dfe8f8 0%,#b8cdf0 30%,#5b78c8 52%,#2f4fa8 70%,#4a3a9c 100%)}
.hero-address{left:78px;top:32px;display:flex;gap:12px;color:var(--purple);font-size:22px;line-height:28px;font-family:'Raleway',sans-serif;font-weight:500}
.hero-call{right:78px;top:26px;display:flex;gap:14px;align-items:center;color:var(--purple);font-family:'Raleway',sans-serif}
.hero-call small{display:block;font-size:19px;font-weight:500}
.hero-call strong{display:block;font-size:32px;font-weight:700}
.hero-rule{left:78px;top:112px;width:1044px;height:1px;background:rgba(74,46,143,.3)}
.brand{left:0;width:1200px;top:200px;display:flex;justify-content:center;align-items:center;gap:18px}
.brand-dot{width:54px;height:54px;border-radius:50%;background:var(--purple)}
.brand-name{font-family:'Raleway',sans-serif;font-weight:700;font-size:50px;color:var(--purple)}
.hero-title{left:0;width:1200px;top:430px;text-align:center;color:var(--white);font-family:'Raleway',sans-serif;font-weight:800;font-size:50px;line-height:62px}
.btn{display:flex;align-items:center;justify-content:center;background:var(--purple);color:var(--white);border-radius:32px;font-family:'Raleway',sans-serif;font-weight:500;text-transform:uppercase}
.hero-btn{left:486px;top:581px;width:227px;height:60px;font-size:25px}

/* nav */
.nav{left:0;top:801px;width:1200px;height:62px;background:var(--purple)}
.nav ul{list-style:none;display:flex;margin-left:78px;height:62px}
.nav li{display:flex;align-items:center;padding:0 35px;color:var(--white);font-family:'Raleway',sans-serif;font-size:19px;font-weight:500}
.nav li.active{background:var(--green)}

/* welcome */
.section-title{left:0;width:1200px;text-align:center;font-family:'Raleway',sans-serif;font-weight:300;font-size:42px;color:#555}
.section-title span{color:var(--purple);font-weight:400}
.welcome-title{top:915px}
.welcome-text{left:180px;width:840px;top:988px;text-align:center;font-size:15px;line-height:26px}
.welcome-text p+p{margin-top:24px}
.read-btn{left:505px;top:1129px;width:190px;height:50px;font-size:22px}

/* appointments */
.appt{left:78px;top:1233px;width:1044px;height:255px;background:var(--grey-bg);border-bottom:4px solid var(--purple);box-shadow:0 30px 30px -18px rgba(0,0,0,.3)}
.appt-notch{left:589px;top:1488px}
.appt-mark{left:150px;top:1257px;width:86px;height:188px;border-radius:40px;background:linear-gradient(180deg,#d6d6d6,#c6c6c6)}
.appt-photo{left:950px;top:1233px;width:172px;height:225px;background:linear-gradient(135deg,#f3f3f3 0%,#e8c6b0 55%,#d9a98d 100%)}
.appt-title{left:0;width:1200px;top:1262px;text-align:center;font-family:'Raleway',sans-serif;font-weight:400;font-size:40px;color:var(--orange)}
.appt-phone{left:0;width:1200px;top:1318px;display:flex;justify-content:center;align-items:center;gap:12px;font-family:'Raleway',sans-serif;font-weight:400;font-size:31px;color:var(--green)}
.appt-phone strong{font-family:'Open Sans',sans-serif;font-weight:700;font-size:32px}
.appt-or{left:0;width:1200px;top:1395px;text-align:center;font-size:19px;color:#555}
.appt-mail{left:0;width:1200px;top:1430px;text-align:center;font-size:21px;color:var(--purple)}

/* services */
.services-title{top:1560px}
.card{top:1637px;width:322px;height:254px;border-bottom:5px solid var(--purple)}
.card-img{width:322px;height:198px}
.card-label{height:51px;background:var(--grey-card);display:flex;align-items:center;justify-content:center;font-family:'Raleway',sans-serif;font-size:21px;color:var(--purple)}
.img-a{background:linear-gradient(135deg,#eef2f5,#d8b9a4 60%,#c7d2dc)}
.img-b{background:linear-gradient(135deg,#c9d8cf,#e8cdbb 50%,#6aa88a)}
.img-c{background:linear-gradient(135deg,#8a5e3e,#b07a52 50%,#4d7fc0)}

/* follow */
.follow{left:0;top:1958px;width:1200px;height:250px;background:var(--grey-bg)}
.follow-photo{left:38px;top:1958px;width:335px;height:232px;background:linear-gradient(160deg,#f0f0f0 10%,#efd2bf 55%,#e6c0a8 80%,#f0f0f0)}
.follow-title{top:1984px}
.follow-badge{left:406px;top:2055px;width:124px;height:124px;border-radius:50%;background:var(--white);border:2px solid #ddd;display:flex;align-items:center;justify-content:center}
.follow-badge i{width:52px;height:52px;border-radius:50%;background:var(--purple)}
.follow-name{left:544px;top:2062px;font-family:'Raleway',sans-serif;font-size:24px;color:var(--purple)}
.like-btn{left:544px;top:2101px;width:203px;height:62px;background:var(--white);border:2px solid var(--purple);border-radius:4px;display:flex;align-items:center;justify-content:center;font-family:'Raleway',sans-serif;font-weight:700;font-size:22px;color:var(--purple)}

/* partners */
.partner{top:2245px;height:90px;border-radius:8px}

/* contact */
.contact{left:0;top:2377px;width:1200px;height:365px;background:var(--purple)}
.contact-title{left:0;width:1200px;top:2420px;text-align:center;font-family:'Raleway',sans-serif;font-weight:400;font-size:40px;color:var(--white)}
.field{background:var(--white);border:1px solid #ccc;font-size:11px;color:#777;padding:9px 10px}
.send{left:462px;top:2606px;width:84px;height:82px;background:var(--purple-mid);display:flex;align-items:center;justify-content:center}
.divider{left:581px;top:2502px;width:1px;height:186px;background:rgba(255,255,255,.35)}
.info{left:605px;color:var(--white);font-size:14px;line-height:22px;display:flex;gap:14px}
.info b{font-weight:700;font-size:15px}
.map{left:862px;top:2502px;width:261px;height:186px;background:linear-gradient(135deg,#e9efe2,#dfe6d8 50%,#f1d9a8)}

.footer{left:0;top:2742px;width:1200px;height:53px;background:var(--purple-dark);display:flex;align-items:center;justify-content:space-between;padding:0 78px}
.footer p{color:var(--white);font-size:14px;font-weight:700}
.footer p span{color:var(--orange)}
.social{display:flex;gap:10px}
.social i{width:28px;height:28px;border-radius:50%;background:rgba(255,255,255,.85)}
</style>
</head>
<body>

<header>
  <div class="abs hero" role="img" aria-label="Photo of bare feet resting on a boat railing over the sea"></div>
  <div class="abs hero-address">
    <svg width="16" height="24" viewBox="0 0 16 24"><path d="M8 0C3.6 0 0 3.5 0 7.8 0 13.6 8 24 8 24s8-10.4 8-16.2C16 3.5 12.4 0 8 0zm0 11a3.2 3.2 0 110-6.4A3.2 3.2 0 018 11z" fill="#4a2e8f"/></svg>
    <div>Suite 208 / 155 Harrow<br>Lane Melbourne 3000</div>
  </div>
  <div class="abs hero-call">
    <svg width="52" height="52" viewBox="0 0 52 52"><circle cx="26" cy="26" r="24" fill="none" stroke="#4a2e8f" stroke-width="2"/><path d="M19 15c1-1 2.5-1 3.300l2.6 3.4c.7 1 .6 2.2-.3 3l-1.5 1.4c1.2 2.6 3.3 4.8 5.9 6l1.5-1.5c.8-.9 2.1-1 3-.3l3.4 2.6c1 .8 1 2.3 0 3.3l-1.6 1.6c-1.6 1.6-4.2 2-6.3.8-5-2.7-9-6.7-11.6-11.7-1.1-2.1-.7-4.6.9-6.2z" fill="#4a2e8f"/></svg>
    <div><small>CALL US NOW!</small><strong>1300 555 274</strong></div>
  </div>
  <div class="abs hero-rule"></div>
  <div class="abs brand"><span class="brand-dot"></span><span class="brand-name">Bramble Ridge Podiatry</span></div>
  <h1 class="abs hero-title">DON'T LET PAIN RUN<br>YOUR LIFE</h1>
  <a class="abs btn hero-btn">Contact Us</a>
</header>

<nav class="abs nav">
  <ul><li class="active">HOME</li><li>ABOUT</li><li>SERVICES</li><li>CONTACT</li></ul>
</nav>

<section>
  <h2 class="abs section-title welcome-title">WELCOME TO <span>BRAMBLE RIDGE PODIATRY</span></h2>
  <div class="abs welcome-text">
    <p>Bramble Ridge Podiatry is a Podiatry clinic in the heart of Melbourne CBD. We are located between Alder &amp; Finch Streets in the Harbourline Business Centre / Wattle Hotel Complex.</p>
    <p>Our podiatrists are fully qualified health professionals who are able to diagnose, treat, manage or help to prevent all medical conditions that affect the feet and lower limb.</p>
  </div>
  <a class="abs btn read-btn">Read More</a>
</section>

<section>
  <div class="abs appt"></div>
  <svg class="abs appt-notch" width="22" height="14" viewBox="0 0 22 14"><path d="M0 0h22L11 14z" fill="#4a2e8f"/></svg>
  <div class="abs appt-mark" role="img" aria-label="Grey footprint illustration"></div>
  <div class="abs appt-photo" role="img" aria-label="Photo of hands massaging a foot"></div>
  <h3 class="abs appt-title">For Appointments or Enquiries</h3>
  <div class="abs appt-phone">Please call us on
    <svg width="50" height="50" viewBox="0 0 52 52"><circle cx="26" cy="26" r="24" fill="none" stroke="#7cc242" stroke-width="2"/><path d="M19 15c1-1 2.5-1 3.3 0l2.6 3.4c.7 1 .6 2.2-.3 3l-1.5 1.4c1.2 2.6 3.3 4.8 5.9 6l1.5-1.5c.8-.9 2.1-1 3-.3l3.4 2.6c1 .8 1 2.3 0 3.3l-1.6 1.6c-1.6 1.6-4.2 2-6.3.8-5-2.7-9-6.7-11.6-11.7-1.1-2.1-.7-4.6.9-6.2z" fill="#7cc242"/></svg>
    <strong>1300 555 274</strong></div>
  <div class="abs appt-or">OR</div>
  <div class="abs appt-mail">Email: <svg width="18" height="14" viewBox="0 0 18 14"><rect x="1" y="1" width="16" height="12" fill="none" stroke="#4a2e8f" stroke-width="1.6"/><path d="M1 1l8 7 8-7" fill="none" stroke="#4a2e8f" stroke-width="1.6"/></svg> info@brambleridgepodiatry.net</div>
</section>

<section>
  <h2 class="abs section-title services-title">SERVICES <span>WE PROVIDE</span></h2>
  <div class="abs card" style="left:78px"><div class="card-img img-a" role="img" aria-label="Photo of a podiatrist examining a foot"></div><div class="card-label">General Treatment</div></div>
  <div class="abs card" style="left:438px"><div class="card-img img-b" role="img" aria-label="Photo of a foot receiving specialised treatment"></div><div class="card-label">Specialised Treatments</div></div>
  <div class="abs card" style="left:799px"><div class="card-img img-c" role="img" aria-label="Photo of a runner bandaging an injured foot beside sneakers"></div><div class="card-label">Sports Injury</div></div>
</section>

<section>
  <div class="abs follow"></div>
  <div class="abs follow-photo" role="img" aria-label="Photo of bare legs and feet"></div>
  <h2 class="abs section-title follow-title">FOLLOW <span>US</span></h2>
  <div class="abs follow-badge"><i></i></div>
  <div class="abs follow-name">Bramble Ridge Podiatry</div>
  <a class="abs like-btn">Like Us</a>
</section>

<section aria-label="Partners">
  <div class="abs partner" style="left:78px;width:230px;background:#e8e3f2"></div>
  <div class="abs partner" style="left:360px;width:215px;background:#e1e8f4"></div>
  <div class="abs partner" style="left:640px;width:220px;background:#e6f2dd"></div>
  <div class="abs partner" style="left:912px;width:240px;background:#ececec"></div>
</section>

<section>
  <div class="abs contact"></div>
  <h2 class="abs contact-title">CONTCT US</h2>
  <div class="abs field" style="left:78px;top:2502px;width:229px;height:41px">Name</div>
  <div class="abs field" style="left:317px;top:2502px;width:229px;height:41px">Phone</div>
  <div class="abs field" style="left:78px;top:2554px;width:468px;height:41px">E-Mail</div>
  <div class="abs field" style="left:78px;top:2606px;width:375px;height:82px">Message</div>
  <div class="abs send"><svg width="34" height="24" viewBox="0 0 34 24"><rect x="1" y="1" width="32" height="22" fill="none" stroke="#fff" stroke-width="2"/><path d="M1 1l16 12L33 1M1 23l12-11M33 23L21 12" fill="none" stroke="#fff" stroke-width="2"/></svg></div>
  <div class="abs divider"></div>
  <div class="abs info" style="top:2502px">
    <svg width="18" height="26" viewBox="0 0 16 24"><path d="M8 1C4.1 1 1 4.1 1 7.8 1 13 8 22.5 8 22.5S15 13 15 7.8C15 4.1 11.9 1 8 1z" fill="none" stroke="#fff" stroke-width="1.4"/><circle cx="8" cy="8" r="2.6" fill="none" stroke="#fff" stroke-width="1.4"/></svg>
    <div><b>bramble ridge podiatry</b><br>Suite 208 / 155 Harrow Lane<br>Melbourne 3000.</div>
  </div>
  <div class="abs info" style="top:2604px">
    <svg width="18" height="18" viewBox="0 0 24 24"><path d="M5 2c1-1 2.4-1 3.2 0l2.4 3.1c.7.9.6 2.1-.2 2.9L9 9.4c1.2 2.5 3.1 4.5 5.6 5.6l1.4-1.4c.8-.8 2-.9 2.9-.2l3.1 2.4c1 .8 1 2.2 0 3.2l-1.5 1.5c-1.5 1.5-3.9 1.9-5.9.8C9.8 18.7 5.3 14.2 2.7 9.4 1.6 7.4 2 5 3.5 3.5z" fill="none" stroke="#fff" stroke-width="1.4"/></svg>
    <div>1300 555 274</div>
  </div>
  <div class="abs info" style="top:2647px">
    <svg width="18" height="14" viewBox="0 0 18 14"><rect x="1" y="1" width="16" height="12" fill="none" stroke="#fff" stroke-width="1.4"/><path d="M1 1l8 7 8-7" fill="none" stroke="#fff" stroke-width="1.4"/></svg>
    <div>info@brambleridgepodiatry.net</div>
  </div>
  <div class="abs map" role="img" aria-label="Street map showing the clinic location"></div>
</section>

<footer class="abs footer">
  <p>© <span>bramble ridge podiatry</span> - 2016. All Rights Reserved.</p>
  <div class="social"><i></i><i></i><i></i><i></i></div>
</footer>

</body>
</html>
```